KLV Plant Services

We are a heavy diesel mechanical business with additional air con certificates, remapping engine rebuilt

Contact Information for Business Card

Company Name, Director Name, Managing Director, Contact details, email and website

Font styles to use
Serif
Script

```html
<!DOCTYPE html>
<html lang="en">
<head>
<meta charset="utf-8">
<title>KLV Plant Services – Business Card</title>
<link href="https://fonts.googleapis.com/css2?family=Playfair+Display:wght@400;700&family=Dancing+Script:wght@500&display=swap" rel="stylesheet">
<style>
  :root {
    --navy: #2b2a7a;
    --ink: #0b0b0c;
    --paper: #f5f5f5;
    --text: #2a2a2a;
    --stage: #e8e5e0;
    --serif: "Playfair Display", Georgia, serif;
    --script: "Dancing Script", cursive;
  }
  * { margin: 0; padding: 0; box-sizing: border-box; }
  html, body { width: 1200px; height: 900px; overflow: hidden; }
  body { background: var(--stage); font-family: var(--serif); position: relative; }

  .card {
    position: absolute; width: 620px; height: 354px;
    background: linear-gradient(120deg, #ffffff, var(--paper));
    overflow: hidden; box-shadow: 0 10px 28px rgba(0,0,0,.18);
  }
  .card--front { left: 70px; top: 70px; }
  .card--back { left: 510px; top: 476px; }
  .card svg.art { position: absolute; inset: 0; }

  /* Front */
  .brand-name { position: absolute; left: 56px; top: 110px; color: var(--navy); font-family: var(--serif); font-weight: 700; line-height: .95; }
  .brand-name .big { display: block; font-size: 118px; letter-spacing: 2px; }
  .brand-name .small { display: block; font-size: 38px; margin-top: 6px; }
  .front-web {
    position: absolute; right: 16px; top: 20px; color: #fff; font-family: var(--serif); font-size: 14px; letter-spacing: 1.5px;
    writing-mode: vertical-rl;
  }

  /* Back */
  .person { position: absolute; left: 28px; top: 146px; }
  .person__name { color: var(--navy); font-family: var(--serif); font-weight: 700; font-size: 21px; letter-spacing: 1px; }
  .person__role { color: #fff; font-family: var(--script); font-weight: 500; font-size: 22px; margin-top: 2px; }

  .logo-lockup { position: absolute; right: 24px; top: 40px; display: flex; align-items: center; gap: 12px; }
  .logo-lockup__dot { width: 26px; height: 26px; border-radius: 50%; background: var(--ink); }
  .logo-lockup__name { color: var(--navy); font-family: var(--serif); font-weight: 700; font-size: 23px; line-height: 1; }

  .contact { position: absolute; left: 312px; top: 192px; list-style: none; color: var(--text); font-family: var(--serif); font-size: 14.5px; }
  .contact li { display: flex; align-items: flex-start; gap: 9px; line-height: 1.3; margin-bottom: 4px; }
  .contact svg { flex: none; width: 14px; height: 14px; margin-top: 3px; fill: var(--navy); }
</style>
</head>
<body>

<section class="card card--front">
  <svg class="art" width="620" height="354" viewBox="0 0 620 354">
    <polygon points="280,0 620,0 620,250 450,290 425,170 260,48" fill="var(--ink)" role="img" aria-label="Excavator arm and bucket silhouette"/>
  </svg>
  <h1 class="brand-name"><span class="big">KLV</span><span class="small">Plant Services</span></h1>
  <p class="front-web">www.klvplantservices.net</p>
</section>

<section class="card card--back">
  <svg class="art" width="620" height="354" viewBox="0 0 620 354">
    <polygon points="0,110 250,28 268,240 350,354 0,354" fill="var(--ink)" role="img" aria-label="Excavator arm and bucket silhouette"/>
  </svg>

  <div class="person">
    <p class="person__name">MARK DALTON</p>
    <p class="person__role">Managing Director</p>
  </div>

  <div class="logo-lockup">
    <span class="logo-lockup__dot"></span>
    <span class="logo-lockup__name">KLV Plant Services</span>
  </div>

  <ul class="contact">
    <li><svg viewBox="0 0 24 24"><path d="M6.6 10.8a15 15 0 0 0 6.6 6.6l2.2-2.2a1 1 0 0 1 1-.25 11.4 11.4 0 0 0 3.6.57 1 1 0 0 1 1 1V20a1 1 0 0 1-1 1A17 17 0 0 1 3 4a1 1 0 0 1 1-1h3.5a1 1 0 0 1 1 1c0 1.250.2 2.45.57 3.57a1 1 0 0 1-.25 1z"/></svg>0412 555 019</li>
    <li><svg viewBox="0 0 24 24"><path d="M2 5h20v14H2zm2 2v.5l8 5 8-5V7l-8 5z"/></svg>admin@klvplantservices.net</li>
    <li><svg viewBox="0 0 24 24"><path d="M12 2a10 10 0 1 0 0 20 10 10 0 0 0 0-20zm6.9 6h-3a15 15 0 0 0-1.3-4 8 8 0 0 1 4.3 4zM12 4c.8 1.2 1.5 2.5 1.9 4h-3.8c.4-1.5 1.1-2.8 1.9-4zM4.3 14a8 8 0 0 1 0-4h3.4a16 16 0 0 0 0 4zm.8 2h3a15 15 0 0 0 1.3 4 8 8 0 0 1-4.3-4zm3-8h-3a8 8 0 0 1 4.3-4 15 15 0 0 0-1.3 4zM12 20c-.8-1.2-1.5-2.5-1.9-4h3.8c-.4 1.5-1.1 2.8-1.9 4zm2.3-6H9.7a14 14 0 0 1 0-4h4.6a14 14 0 0 1 0 4zm.3 5.6a15 15 0 0 0 1.3-3.6h3a8 8 0 0 1-4.3 3.6zm1.7-5.6a16 16 0 0 0 0-4h3.4a8 8 0 0 1 0 4z"/></svg>www.klvplantservices.net</li>
    <li><svg viewBox="0 0 24 24"><path d="M12 2a7 7 0 0 0-7 7c0 5 7 13 7 13s7-8 7-13a7 7 0 0 0-7-7zm0 9.5A2.5 2.5 0 1 1 12 6.5a2.5 2.5 0 0 1 0 5z"/></svg><span>17 Banksia Road, Kalamunda<br>WA 6076, Australia</span></li>
  </ul>
</section>

</body>
</html>
```